OBK Farcoast Logistics Limited

We need the buissnes card to be very exclusive. As we are all young in our company. We need this to be the gate to make our clients feel deep interest for us.

We are focused in as International Trade advisors, and our products go from Oil Tanker Ships to Rubber balls for dogs.

Our Slogan is Linking World Trade.
And our main marketing will be through Internet.

We were stablished in 2009 In Mexico and we also have offices in Hong Kong.
We have representatives in China and Europe.

Target Market(s)

Is every company or Individual that wants to develop an International Project or product development or Logistic service of Goods and people.
Some of our current projects are Ship Brokerage, Mine Brokerage, Real State and Product Pormotional development.

Industry/Entity Type

It Company

Requirements
Must have
• Our Logo and slogan, and make the card accoriding to the logo.
Nice to have
• Our Colors

```html
<!DOCTYPE html>
<html lang="en">
<head>
<meta charset="utf-8">
<title>OBK Farcoast Logistics Limited – Business Card</title>
<link href="https://fonts.googleapis.com/css2?family=Open+Sans:wght@400;600;700&display=swap" rel="stylesheet">
<style>
  :root {
    --backdrop: #ece7e1;
    --card: #ffffff;
    --green: #8cc63f;
    --blue: #1c8fd0;
    --sky: #3fb2e6;
    --navy: #2e3f95;
    --ink: #1a1a1a;
  }
  * { margin: 0; padding: 0; box-sizing: border-box; }
  html, body { width: 1200px; height: 989px; overflow: hidden; }
  body {
    background: var(--backdrop);
    font-family: "Open Sans", Arial, sans-serif;
    color: var(--ink);
    position: relative;
  }
  .card {
    position: absolute;
    top: 59px;
    width: 494px;
    height: 867px;
    background: var(--card);
    box-shadow: 0 2px 6px rgba(0,0,0,.18);
  }
  .card--front { left: 66px; }
  .card--back { left: 616px; }

  .band {
    position: absolute; left: 0; width: 100%; height: 56px;
    background: var(--green);
    display: flex; align-items: center; justify-content: center;
  }
  .band--top { top: 0; }
  .band--bottom { bottom: 0; }
  .rule {
    position: absolute; left: 0; width: 100%;
    border-top: 2px solid var(--blue);
    border-bottom: 1px solid var(--sky);
    height: 5px;
  }
  .rule--top { top: 58px; }
  .rule--bottom { bottom: 58px; }

  .holder-name { font-size: 25px; font-weight: 700; color: var(--ink); }
  .holder-name span { font-weight: 400; font-size: 21px; }

  .brand-mark {
    position: absolute; left: 50%; transform: translateX(-50%);
    border-radius: 50%;
    background: var(--sky);
  }
  .card--front .brand-mark { top: 130px; width: 260px; height: 260px; }
  .card--back .brand-mark { top: 250px; width: 280px; height: 280px; }

  .brand-name {
    position: absolute; left: 0; width: 100%;
    text-align: center;
    color: var(--green); font-weight: 600;
    letter-spacing: 6px; line-height: 1;
  }
  .card--front .brand-name { top: 420px; font-size: 84px; }
  .card--back .brand-name { top: 560px; font-size: 40px; }

  .slogan {
    position: absolute; top: 527px; left: 0; width: 100%;
    text-align: center; color: var(--blue);
    font-size: 19px;
  }

  .contact {
    position: absolute; left: 0; width: 100%;
    text-align: center; font-size: 20px;
    display: flex; justify-content: center; align-items: center; gap: 8px;
  }
  .contact svg { width: 18px; height: 18px; fill: var(--blue); }
  .contact--phones { top: 632px; }
  .contact--phones .sep { width: 10px; }
  .contact--email { top: 675px; }
  .contact--address { top: 740px; font-size: 20px; }

  .web { font-size: 20px; letter-spacing: 2px; color: var(--ink); }
  .web--back {
    position: absolute; left: 0; width: 100%; top: 820px;
    text-align: center; font-size: 22px; letter-spacing: 4px;
  }
  .web--back .domain { color: var(--blue); }
</style>
</head>
<body>

  <section class="card card--front" aria-label="Card front">
    <header class="band band--top">
      <p class="holder-name">Your Name, <span>Position</span></p>
    </header>
    <div class="rule rule--top"></div>

    <div class="brand-mark" aria-hidden="true"></div>
    <p class="brand-name">OBK</p>
    <p class="slogan">Linking World Trade</p>

    <p class="contact contact--phones">
      <svg viewBox="0 0 24 24" aria-hidden="true"><path d="M6.6 10.8a15 15 0 0 0 6.6 6.6l2.2-2.2a1 1 0 0 1 1-.25 11.4 11.4 0 0 0 3.6.57 1 1 0 0 1 1 1V20a1 1 0 0 1-1 1A17 17 0 0 1 3 4a1 1 0 0 1 1-1h3.5a1 1 0 0 1 1 1c0 1.25.2 2.45.57 3.57a1 1 0 0 1-.25 1z"/></svg>
      <span>123-456-7890</span>
      <span class="sep"></span>
      <svg viewBox="0 0 24 24" aria-hidden="true"><path d="M7 1h10a2 2 0 0 1 2 2v18a2 2 0 0 1-2 2H7a2 2 0 0 1-2-2V3a2 2 0 0 1 2-2zm0 3v14h10V4zm5 15.5a1 1 0 1 0 0 2 1 1 0 0 0 0-2z"/></svg>
      <span>123-456-7890</span>
    </p>
    <p class="contact contact--email">
      <svg viewBox="0 0 24 24" aria-hidden="true"><path d="M2 5h20v14H2zm2 2v.4l8 5 8-5V7zm0 2.8V17h16V9.8l-8 5z"/></svg>
      <span>info@farcoastobk.com</span>
    </p>
    <p class="contact contact--address">00, Complex Name, City, State, 00045</p>

    <div class="rule rule--bottom"></div>
    <footer class="band band--bottom">
      <p class="web">www.farcoastobk.com</p>
    </footer>
  </section>

  <section class="card card--back" aria-label="Card back">
    <div class="brand-mark" aria-hidden="true"></div>
    <p class="brand-name">OBK</p>
    <p class="web web--back">www.<span class="domain">farcoastobk</span>.com</p>
  </section>

</body>
</html>
```